A parent Company needs a website as a leading diversified business in industrial Conglomerates in Af

Velkor Group is a private (Holding) limited liability company incorporated under the Companies Code, 1963 (Act 179) in November, 2013 to following the speedy growth in numbers of its current subsidiaries which has been founded several years ago with an emerging force to become one of the largest and a leading diversified business in industrial Conglomerates in Africa.
The Group which is 100% wholly owned indigenous Ghanaian Company focuses on provision of local, value-added products and services that meet the needs of the African population. The Group is headquartered in Accra, Ghana with interests across a range of sectors in Africa.
We are currently into Food & Beverage, Real Estate Development, Transportation, Health Care, Consumer Products Distribution, Agro Processing, Manufacturing, ICT, Exports & Import, and still counting.
In the next 3 years, we shall announce our ambitions to enter Ghana's largest Oil and Gas industry, playing a strategic role in the petroleum sector with strategic alliances, and help build Ghana's biggest and most important Energy sector in the country.
Inspired by billionaires Tom Prewitt, Harlan Voskel, and Emeka Ofodile, Velkor Group (Velkor Foundation) is committed to making a name for itself on the philanthropic circuit and has given away privately and still given to the cause to the needy in the society and some specific social causes in Ghana.
The company is managed by a 5 member board and a 2 member advisory experts who are non-board members.
The company has a vision, mission and it is guided by its core values.
We would like to see a designs that is very professional and looks corporate and can attract investors and partners. It must communicate financial safety and growth and must reflect our logo colors.

```html
<!DOCTYPE html>
<html lang="en">
<head>
<meta charset="utf-8">
<title>Velkor Group — Tenacity, Integrity &amp; Passion</title>
<link rel="stylesheet" href="https://fonts.googleapis.com/css2?family=Open+Sans:wght@400;600&display=swap">
<style>
:root{
  --blue:#0a9fe0;
  --navy:#0b5aa8;
  --red:#e30613;
  --ink:#333;
  --muted:#777;
  --grey-band:#edebeb;
  --dark:#1c1c1c;
  --footer:#2b2b2b;
  --orange:#f39a5b;
}
*{margin:0;padding:0;box-sizing:border-box}
html,body{width:862px;height:1200px;overflow:hidden;background:#fff}
body{font-family:"Open Sans",sans-serif;color:var(--ink);position:relative}
.abs{position:absolute}

/* header */
.site-header{position:absolute;left:0;top:0;width:862px;height:66px;background:#fff;border-bottom:1px solid #ddd}
.brand{left:80px;top:18px;display:flex;align-items:center;gap:6px}
.brand-mark{width:30px;height:30px;border-radius:50%;background:var(--blue)}
.brand-name{font-size:15px;font-weight:600;color:#222;letter-spacing:.3px;line-height:1}
.brand-tag{left:116px;top:48px;font-size:8px;color:var(--red)}
.utility{left:628px;top:0;width:154px;height:22px;background:var(--navy);color:#fff;font-size:8.5px;font-weight:600;display:flex;align-items:center;justify-content:center;gap:5px;border-radius:0 0 3px 3px}
.main-nav{left:295px;top:33px;display:flex;align-items:center;font-size:9.5px;font-weight:600;color:#555}
.main-nav span{margin-right:20px}
.main-nav .active{background:var(--blue);color:#fff;padding:3px 9px;margin-right:10px}

/* hero */
.hero-band{left:0;top:66px;width:862px;height:233px;background:linear-gradient(90deg,#2a2a2a,#161616 50%,#2a2a2a)}
.hero-title{left:0;top:108px;width:862px;text-align:center;font-size:24px;color:#fff;letter-spacing:-.3px}
.hero-title em{font-style:normal;color:var(--red)}
.hero-photo{left:106px;top:180px;width:646px;height:210px;background:linear-gradient(90deg,#c9c2b8,#e8e4de 40%,#6e7584 70%,#2f3442);box-shadow:0 10px 14px -8px rgba(0,0,0,.45)}

/* welcome */
.world-map{left:112px;top:428px;width:256px;height:144px;background:radial-gradient(ellipse at 60% 50%,#c8c8c8,#e2e2e2 70%,#fff)}
.welcome-title{left:398px;top:434px;font-size:19px;color:#222}
.welcome-title b{font-weight:400;font-size:22px}
.welcome-tag{left:399px;top:459px;font-size:14px;color:var(--red)}
.welcome-copy{left:401px;top:489px;width:351px;font-size:9px;line-height:13.3px;color:var(--muted);text-align:justify}

/* sectors */
.sector-band{left:0;top:599px;width:862px;height:225px;background:var(--grey-band)}
.sector{top:622px;width:200px;text-align:center}
.sector-icon{width:56px;height:56px;border-radius:50%;background:var(--blue);margin:0 auto;display:flex;align-items:center;justify-content:center}
.sector h3{font-weight:400;font-size:15px;color:var(--blue);margin-top:12px}
.sector p{font-size:9.3px;line-height:12.2px;color:#555;margin-top:4px;padding:0 16px}
.sector .more{display:inline-flex;align-items:center;gap:6px;font-size:9.5px;color:var(--red);margin-top:15px}

/* info cards */
.info{top:858px;width:205px}
.info h4{font-weight:400;font-size:11.5px;color:#222;margin-bottom:4px}
.info-photo{width:183px;height:92px;border:1px solid #ccc}
.info p{font-size:7.5px;line-height:10.3px;color:#444;margin-top:12px}
.info a{display:block;font-size:8.5px;color:var(--red);text-decoration:underline;margin-top:12px}

/* footer */
.site-footer{left:0;top:1085px;width:862px;height:115px;background:var(--footer)}
.foot-col{top:1100px;font-size:8.3px;color:#ccc;line-height:10px}
.foot-col h5{font-weight:400;font-size:10px;color:#999;margin-bottom:12px}
.foot-pitch{left:464px;top:1101px;font-size:9.3px;color:#fff}
.foot-call{left:464px;top:1116px;font-size:20px;color:#fff}
.foot-rule{left:80px;top:1158px;width:702px;height:1px;background:#444}
.legal{left:80px;top:1172px;font-size:8.5px;color:#999;word-spacing:1px}
.help-line{left:512px;top:1196px;width:350px;height:4px;background:var(--orange)}
.help-tab{left:684px;top:1170px;width:92px;height:30px;background:var(--orange);border-radius:8px 8px 0 0;font-size:9.5px;font-weight:600;color:#222;display:flex;align-items:center;justify-content:center;gap:10px}
</style>
</head>
<body>

<header class="site-header">
  <div class="abs brand"><span class="brand-mark"></span><span class="brand-name">VELKOR GROUP</span></div>
  <div class="abs brand-tag">Tenacity, Integrity &amp; Passion</div>
  <div class="abs utility"><span>About Us</span>|<span>Support</span>|<span>Contact Us</span></div>
  <nav class="abs main-nav">
    <span class="active">Home</span><span>Food &amp; Beverage</span><span>Transportation</span><span>Health Care</span><span>Agro Processing</span><span>Exports &amp; Import</span>
  </nav>
</header>

<section>
  <div class="abs hero-band"></div>
  <h1 class="abs hero-title" style="font-weight:400"><em>Velkor Group</em> Tenacity, integrity &amp; Passion</h1>
  <div class="abs hero-photo" role="img" aria-label="Business team smiling around a meeting table"></div>
</section>

<section>
  <div class="abs world-map" role="img" aria-label="World map highlighting the Americas and operating countries in red"></div>
  <h2 class="abs welcome-title" style="font-weight:400">Welcome to <b>VELKOR Group</b></h2>
  <div class="abs welcome-tag">Tenacity, Integrity &amp; Passion</div>
  <p class="abs welcome-copy">Velkor Group is a private (Holding) limited liability company incorporated under the Companies Code, 1963 (Act 179) in November, 2013 to following the speedy growth in numbers of its current subsidiaries which has been founded several years ago with an emerging force to become one of the largest and a leading diversified business in industrial Conglomerates in Africa.</p>
</section>

<section>
  <div class="abs sector-band"></div>
  <div class="abs sector" style="left:80px">
    <div class="sector-icon"><svg width="26" height="30" viewBox="0 0 26 30" fill="#fff"><rect x="3" y="2" width="2" height="10"/><rect x="7" y="2" width="2" height="10"/><rect x="11" y="2" width="2" height="10"/><rect x="3" y="10" width="10" height="4" rx="2"/><rect x="6" y="12" width="4" height="16" rx="2"/><path d="M18 2c4 0 5 6 5 12h-2v14h-4z"/></svg></div>
    <h3>Food &amp; Beverages</h3>
    <p>Lorem Ipsum is simply dummy text of the printing and typesetting industry. Lorem Ipsum has been the industry's standard dummy text ever</p>
    <span class="more"><svg width="7" height="11" viewBox="0 0 7 11"><path d="M1 1l4.5 4.5L1 10" stroke="#222" stroke-width="2" fill="none"/></svg>Read More</span>
  </div>
  <div class="abs sector" style="left:320px">
    <div class="sector-icon"><svg width="34" height="24" viewBox="0 0 34 24" fill="#fff"><rect x="1" y="3" width="20" height="14"/><path d="M22 7h6l4 5v5H22z"/><circle cx="8" cy="19" r="3.5" stroke="#0a9fe0" stroke-width="1.5"/><circle cx="26" cy="19" r="3.5" stroke="#0a9fe0" stroke-width="1.5"/></svg></div>
    <h3>Transportation</h3>
    <p>Lorem Ipsum is simply dummy text of the printing and typesetting industry. Lorem Ipsum has been the industry's standard dummy text ever</p>
    <span class="more"><svg width="7" height="11" viewBox="0 0 7 11"><path d="M1 1l4.5 4.5L1 10" stroke="#222" stroke-width="2" fill="none"/></svg>Read More</span>
  </div>
  <div class="abs sector" style="left:557px">
    <div class="sector-icon"><svg width="26" height="26" viewBox="0 0 26 26"><rect x="2" y="2" width="22" height="22" fill="none" stroke="#fff" stroke-width="2"/><path d="M5 14h5l2-5 3 9 2-4h4" fill="none" stroke="#fff" stroke-width="1.8"/></svg></div>
    <h3>Health &amp; Care</h3>
    <p>Lorem Ipsum is simply dummy text of the printing and typesetting industry. Lorem Ipsum has been the industry's standard dummy text ever</p>
    <span class="more"><svg width="7" height="11" viewBox="0 0 7 11"><path d="M1 1l4.5 4.5L1 10" stroke="#222" stroke-width="2" fill="none"/></svg>Read More</span>
  </div>
</section>

<section>
  <div class="abs info" style="left:88px">
    <h4>Our Vision</h4>
    <div class="info-photo" role="img" aria-label="Businessman in a suit in a bright office" style="background:linear-gradient(90deg,#4a4f5c,#8a8f99 60%,#c8d3a8)"></div>
    <p>Lorem Ipsum is simply dummy text of the printing and typesetting industry. Lorem Ipsum has been the industry's standard dummy text ever since the 1500s, when an unknown printer took a galley of type sheets containing Lorem Ipsum passages.</p>
    <a>Read more</a>
  </div>
  <div class="abs info" style="left:338px">
    <h4>Our Mission</h4>
    <div class="info-photo" role="img" aria-label="Hands holding soil with a young green seedling" style="background:linear-gradient(180deg,#f3eee2,#d9c9a8 50%,#6b4a30)"></div>
    <p>Lorem Ipsum is simply dummy text of the printing and typesetting industry. Lorem Ipsum has been the industry's standard dummy text ever since the 1500s, when an unknown printer took a galley of type sheets containing Lorem Ipsum passages.</p>
    <a>Read more</a>
  </div>
  <div class="abs info" style="left:589px">
    <h4>Our Partners</h4>
    <div class="info-photo" role="img" aria-label="Business partners shaking hands" style="background:linear-gradient(90deg,#2f3d5c,#7f8fa8 50%,#c4ccd8)"></div>
    <p>Lorem Ipsum is simply dummy text of the printing and typesetting industry. Lorem Ipsum has been the industry's standard dummy text ever since the 1500s, when an unknown printer took a galley of type sheets containing Lorem Ipsum passages.</p>
    <a>Read more</a>
  </div>
</section>

<footer>
  <div class="abs site-footer"></div>
  <div class="abs foot-col" style="left:81px"><h5>Home</h5>Food &amp; Beverage<br>Transportation</div>
  <div class="abs foot-col" style="left:172px"><h5>About Us</h5>Lorem amet<br>Lipsum</div>
  <div class="abs foot-col" style="left:273px"><h5>Contact Us</h5>Lorem Lipsum<br>Amet Dor</div>
  <div class="abs foot-col" style="left:370px"><h5>Links</h5>Lorem<br>Lipsum</div>
  <div class="abs foot-pitch">We will advise you, free of charge, without obligation and individual!</div>
  <div class="abs foot-call">Call : +233-0-302-4418</div>
  <div class="abs foot-rule"></div>
  <div class="abs legal">2014, VELKOR Group. Privacy Policy &nbsp;| &nbsp;Terms of Service &nbsp;| &nbsp;Help &nbsp;| &nbsp;Contact</div>
  <div class="abs help-line"></div>
  <div class="abs help-tab">Need Help? <svg width="10" height="10" viewBox="0 0 10 10"><path d="M5 0v10M0 5h10" stroke="#222" stroke-width="2.4"/></svg></div>
</footer>

</body>
</html>
```